Flyer to advertise gutter cleaning throughout the Autumn and winter monthss

I need a new flyer to advertise gutter and driveway cleaning, roof and gutter repairs.

I am an experienced licensed Plumber and Gasfitter looking to broaden my scope of work to gutter cleaning. I am experienced in cleaning gutter and live in a area with large gum trees. I wont something that's clear, eye catching but not too busy.

Flyer requirements: Free roof inspection - no obligation. Gutter Cleaning from $199. Pictures of men using blower or hands to clean roof gutters (no obvious faces) to be included. Australian looking houses.

A mention that 'All general plumbing maintenance' is offered as other services but not too much wording about this as the target is for gutter cleaning.

Phone number: 0427 385 912 (in this format)
Business Name: Larkvale Plumbing & Gasfitting
License: 3175420
ABN: 71364058227
Web: http://larkvaleplumbing.example.site/

Target Market(s)

Elderly - busy working class

Industry/Entity Type

Plumber

Font styles to use
Sans Serif

Colors
0355a3
fbed22
ec1f27
f78f20

Requirements
Must have
• Roof Gutter Cleaning pictures
• Men in protective clothing if possible
Nice to have
• More information:
• Prevent against flooding, mold, rust, rotting and corrosion now!
• Gutter Cleaning Services
• • Remove leaves, sticks, and other debris
• • Clear away clogs
• • Test your downpipes
• • Pinpoint any gutter issues
• • Repair gutter
• With regular service, you can count on your property to be well-protected no matter what the forecast!
Should not have
• Houses that don't look Australian

```html
<!DOCTYPE html>
<html lang="en">
<head>
<meta charset="utf-8">
<title>Larkvale Plumbing &amp; Gasfitting – Gutter Cleaning Flyer</title>
<link rel="stylesheet" href="https://fonts.googleapis.com/css2?family=Oswald:wght@500;700&family=Lato:wght@400;700&display=swap">
<style>
  :root{
    --blue:#0355a3;
    --blue-light:#1f6fc9;
    --red:#ec1f27;
    --pink-red:#e8194a;
    --yellow:#fbed22;
    --grey-text:#555b61;
    --grey-box:#c9c9c9;
    --ink:#231f20;
    --page:#e9ecef;
    --white:#ffffff;
  }
  *{box-sizing:border-box;margin:0;padding:0}
  html,body{width:1200px;height:1200px;overflow:hidden;background:var(--page)}
  body{position:relative;font-family:"Lato",Arial,sans-serif}

  .flyer{
    position:absolute;left:196px;top:30px;width:842px;height:1188px;
    background:var(--white);transform:scale(0.96);transform-origin:top left;
    overflow:hidden;box-shadow:0 4px 18px rgba(0,0,0,.18);
  }
  .hero{position:absolute;left:0;top:0;width:842px;height:480px}

  .badge{
    position:absolute;left:600px;top:285px;width:212px;height:212px;border-radius:50%;
    background:var(--white);border:5px solid var(--yellow);
    display:flex;flex-direction:column;align-items:center;justify-content:center;
    font-family:"Oswald",sans-serif;text-align:center;box-shadow:0 2px 6px rgba(0,0,0,.2);z-index:3;
  }
  .badge-free{font-size:70px;font-weight:700;color:var(--pink-red);line-height:1;margin-top:-6px}
  .badge-line{font-size:21px;font-weight:700;line-height:1.15}
  .badge-line.blue{color:var(--blue)}
  .badge-line.dark{color:var(--ink)}

  .brand{position:absolute;left:38px;top:476px;display:flex;align-items:center;gap:14px}
  .brand-dot{width:100px;height:100px;border-radius:50%;background:var(--blue)}
  .brand-name{font-size:22px;font-weight:700;color:var(--ink);line-height:1.15;width:210px}

  .headline{position:absolute;left:38px;top:600px;width:326px;height:290px;overflow:visible}
  .headline text{font-family:"Oswald",sans-serif;font-weight:700}
  .h-grey{fill:var(--grey-text)}
  .h-blue{fill:var(--blue)}

  .other-services{position:absolute;left:38px;top:906px;width:332px;font-size:16px;color:var(--grey-text);line-height:1.3}

  .call{
    position:absolute;left:92px;top:992px;width:206px;height:74px;border:2px solid #cfcfcf;border-radius:12px;
    text-align:center;background:var(--white);box-shadow:0 6px 6px -4px rgba(0,0,0,.25);
  }
  .call-title{font-size:27px;color:var(--grey-text);margin-top:4px;line-height:1.1}
  .call-number{font-size:24px;color:var(--pink-red);display:flex;align-items:center;justify-content:center;gap:8px}

  .services{
    position:absolute;left:432px;top:470px;width:372px;height:420px;
    background:linear-gradient(180deg,var(--blue-light),var(--blue));border-radius:0 0 14px 14px;
    color:var(--white);padding:52px 24px 0 28px;
  }
  .services-lead{font-size:19px;font-weight:700;line-height:1.27}
  .services-title{font-size:17px;font-weight:700;color:var(--yellow);margin-top:22px}
  .services-list{list-style:none;margin-top:6px}
  .services-list li{display:flex;align-items:center;gap:12px;font-size:16.5px;height:31px;margin-left:4px}
  .services-close{font-size:19px;line-height:1.27;margin-top:16px;text-align:justify}

  .price{
    position:absolute;left:445px;top:915px;width:346px;height:138px;background:var(--grey-box);padding:12px 16px;
    box-shadow:0 8px 8px -6px rgba(0,0,0,.35);
  }
  .price-frame{border:2px dashed var(--white);height:100%;text-align:center;font-family:"Oswald",sans-serif;font-weight:700;color:var(--grey-text)}
  .price-label{font-size:27px;line-height:1;padding-top:15px;font-weight:500;letter-spacing:.5px}
  .price-value{font-size:54px;line-height:1.05}
  .price-value em{font-style:normal;color:var(--pink-red)}

  .footer{position:absolute;left:0;top:1060px;width:842px;height:128px}
  .footer-name{position:absolute;left:0;right:0;top:1112px;text-align:center;color:var(--white);font-size:17px;font-weight:700;text-transform:uppercase}
  .footer-details{position:absolute;left:66px;top:1145px;display:flex;gap:48px;color:var(--white);font-size:17px}
  .footer-details b{font-weight:700}
</style>
</head>
<body>
<main class="flyer">
  <svg class="hero" viewBox="0 0 842 480">
    <defs>
      <linearGradient id="photoTone" x1="0" y1="0" x2="0" y2="1">
        <stop offset="0" stop-color="#8a5a48"/>
        <stop offset=".45" stop-color="#9c7a3e"/>
        <stop offset="1" stop-color="#b86a4e"/>
      </linearGradient>
    </defs>
    <path role="img" aria-label="Photo: gloved hands clearing autumn leaves from a roof gutter" d="M0 0H842V300C700 400 420 445 0 385Z" fill="url(#photoTone)"/>
    <path d="M0 385C420 445 700 400 842 300V318C700 420 430 470 0 410Z" fill="var(--blue)"/>
    <path d="M230 462C520 470 740 420 842 330V345C740 440 520 480 230 462Z" fill="var(--red)"/>
  </svg>

  <div class="badge">
    <div class="badge-free">FREE</div>
    <div class="badge-line blue">ROOF INSPECTION</div>
    <div class="badge-line dark">NO OBLIGATION</div>
  </div>

  <div class="brand">
    <div class="brand-dot"></div>
    <div class="brand-name">Larkvale Plumbing &amp; Gasfitting</div>
  </div>

  <h1 class="headline">
    <svg width="326" height="290" viewBox="0 0 326 290" role="img" aria-label="Gutter &amp; Driveway Cleaning, Roof &amp; Gutter Repairs">
      <text class="h-grey" x="0" y="55" font-size="42" textLength="326" lengthAdjust="spacingAndGlyphs">GUTTER &amp; DRIVEWAY</text>
      <text class="h-blue" x="0" y="133" font-size="80" textLength="326" lengthAdjust="spacingAndGlyphs">CLEANING</text>
      <text class="h-grey" x="0" y="193" font-size="60" textLength="326" lengthAdjust="spacingAndGlyphs">ROOF &amp; GUTTER</text>
      <text class="h-blue" x="0" y="283" font-size="95" textLength="326" lengthAdjust="spacingAndGlyphs">REPAIRS</text>
    </svg>
  </h1>

  <p class="other-services">All general plumbing maintenance is also offered &ndash; just ask us about any other plumbing and gasfitting jobs.</p>

  <div class="call">
    <div class="call-title">CALL US NOW</div>
    <div class="call-number">
      <svg width="20" height="20" viewBox="0 0 20 20"><circle cx="10" cy="10" r="9" fill="var(--blue)"/><path d="M6.5 5.5l2 0 1 2.5-1.3 1c.6 1.3 1.5 2.2 2.8 2.8l1-1.3 2.5 1v2c-4.8.3-8.3-3.2-8-8z" fill="var(--white)"/></svg>
      0427 385 912
    </div>
  </div>

  <section class="services">
    <p class="services-lead">Prevent against flooding, mold, rust, rotting and corrosion now!</p>
    <h2 class="services-title">Gutter Cleaning Services</h2>
    <ul class="services-list">
      <li><svg width="14" height="14" viewBox="0 0 14 14"><rect x="1" y="2" width="11" height="11" fill="none" stroke="var(--yellow)" stroke-width="1.5"/><path d="M3.5 7l2.5 2.5 6-7" fill="none" stroke="var(--yellow)" stroke-width="1.6"/></svg>Remove leaves, sticks, and other debris</li>
      <li><svg width="14" height="14" viewBox="0 0 14 14"><rect x="1" y="2" width="11" height="11" fill="none" stroke="var(--yellow)" stroke-width="1.5"/><path d="M3.5 7l2.5 2.5 6-7" fill="none" stroke="var(--yellow)" stroke-width="1.6"/></svg>Clear away clogs</li>
      <li><svg width="14" height="14" viewBox="0 0 14 14"><rect x="1" y="2" width="11" height="11" fill="none" stroke="var(--yellow)" stroke-width="1.5"/><path d="M3.5 7l2.5 2.5 6-7" fill="none" stroke="var(--yellow)" stroke-width="1.6"/></svg>Test your downpipes</li>
      <li><svg width="14" height="14" viewBox="0 0 14 14"><rect x="1" y="2" width="11" height="11" fill="none" stroke="var(--yellow)" stroke-width="1.5"/><path d="M3.5 7l2.5 2.5 6-7" fill="none" stroke="var(--yellow)" stroke-width="1.6"/></svg>Pinpoint any gutter issues</li>
      <li><svg width="14" height="14" viewBox="0 0 14 14"><rect x="1" y="2" width="11" height="11" fill="none" stroke="var(--yellow)" stroke-width="1.5"/><path d="M3.5 7l2.5 2.5 6-7" fill="none" stroke="var(--yellow)" stroke-width="1.6"/></svg>Repair gutter</li>
    </ul>
    <p class="services-close">With regular service, you can count on your property to be well-protected no matter what the forecast!</p>
  </section>

  <div class="price">
    <div class="price-frame">
      <div class="price-label">GUTTER CLEANING</div>
      <div class="price-value">FROM <em>$199</em></div>
    </div>
  </div>

  <svg class="footer" viewBox="0 0 842 128" aria-hidden="true">
    <path d="M0 50C300 0 620 10 842 60V128H0Z" fill="var(--ink)"/>
    <path d="M0 44C300 -6 620 4 842 54V60C620 12 300 4 0 50Z" fill="var(--white)"/>
    <path d="M0 36C300 -14 620 -4 842 46V54C620 6 300 -4 0 44Z" fill="var(--blue)"/>
    <path d="M330 6C520 -2 700 12 842 40V46C700 18 520 4 330 6Z" fill="var(--red)"/>
  </svg>
  <div class="footer-name">Larkvale Plumbing &amp; Gasfitting</div>
  <div class="footer-details">
    <span><b>License:</b> 3175420</span>
    <span><b>ABN:</b> 71364058227</span>
    <span><b>Web:</b> http://larkvaleplumbing.example.site/</span>
  </div>
</main>
</body>
</html>
```